Harborview Estates Business Card for Apartment Buildings

Create business cards for resident managers who run apartment buildings. The audience is the public who are searching for apartment rentals, and current residents who live at the apartment building. Key design element will be incorporating the company logo, however, the logo cannot dominate. The building name and manager name are more important than the logo. Current business card design leaves little room for copy, so we may need to reduce the size on the current card to allow for more space for copy.

Target Market(s)

Adults 18-65 years of age, who are looking for an apartment rental, plus current residents who live at our apartment buildings.

Industry/Entity Type

Property Management

Contact Information for Business Card

A major design element will be use of the company logo. Important property and manager contact information must be part of the design. The size of the logo will need to be reduced to make room for building and manager contact copy.

Font styles to use
Sans Serif

Colors
3176b5
000000
959595
ffffff

Requirements
Must have
• 1) Incorporate the company logo.
• 2) Use the company colors (dark blue, black/grey, over white).
• 3) FEATURE THE BUILDING NAME
• 4) FEATURE THE MANAGER NAME
• 5) The company name is less important than BUILDING and MANAGER
• 6) Manager contact information
• **SEE ATTACHED CREATIVE BRIEF**
Nice to have
• 1) Back of card logo watermark
• 2) Ability to write notes on back of carfd
Should not have
• Avoid letting the company logo dominate the card, the building name and manager are more important than the company logo.

```html
<!DOCTYPE html>
<html lang="en">
<head>
<meta charset="utf-8">
<title>Harborview Estates – Resident Manager Business Card</title>
<link href="https://fonts.googleapis.com/css2?family=Oswald:wght@500&family=Work+Sans:wght@400;500;700&display=swap" rel="stylesheet">
<style>
  :root {
    --brand-blue: #3176b5;
    --card-black: #232323;
    --stage: #161616;
    --grey: #959595;
    --white: #ffffff;
  }
  * { margin: 0; padding: 0; box-sizing: border-box; }
  html, body { width: 1200px; height: 900px; overflow: hidden; }
  body {
    background: var(--stage);
    font-family: "Work Sans", Arial, sans-serif;
    color: var(--white);
    position: relative;
  }
  .card {
    position: absolute;
    left: 250px;
    width: 700px;
    height: 400px;
    background: var(--card-black);
  }
  .card--front { top: 30px; }
  .card--back { top: 470px; }

  /* Front */
  .brand {
    position: absolute;
    top: 130px;
    left: 0;
    width: 100%;
    display: flex;
    justify-content: center;
    align-items: center;
    gap: 18px;
  }
  .brand__square {
    width: 48px;
    height: 48px;
    background: var(--grey);
  }
  .brand__name {
    font-weight: 700;
    font-size: 40px;
    letter-spacing: 1px;
    color: var(--grey);
    text-transform: uppercase;
    line-height: 1;
  }
  .front__web {
    position: absolute;
    top: 300px;
    width: 100%;
    text-align: center;
    font-size: 19px;
    letter-spacing: 3px;
  }
  .accent { color: var(--brand-blue); }

  /* Back */
  .manager {
    position: absolute;
    top: 150px;
    left: 40px;
    width: 290px;
    text-align: right;
  }
  .manager__name {
    font-family: "Oswald", "Arial Narrow", sans-serif;
    font-weight: 500;
    font-size: 38px;
    color: var(--brand-blue);
    text-transform: uppercase;
    line-height: 1.1;
  }
  .manager__title {
    font-size: 18px;
    letter-spacing: 1px;
    margin-top: 6px;
  }
  .divider {
    position: absolute;
    left: 360px;
    top: 140px;
    width: 2px;
    height: 120px;
    background: var(--brand-blue);
  }
  .contacts {
    position: absolute;
    left: 385px;
    top: 130px;
    list-style: none;
  }
  .contacts li {
    display: flex;
    align-items: center;
    gap: 14px;
    font-size: 17px;
    letter-spacing: 1px;
    line-height: 27px;
  }
  .contacts svg { width: 16px; height: 16px; flex: none; }
  .property {
    position: absolute;
    top: 318px;
    left: 0;
    width: 100%;
    text-align: center;
  }
  .property__name {
    font-weight: 500;
    font-size: 19px;
    color: var(--brand-blue);
    text-transform: uppercase;
  }
  .property__address {
    font-size: 18px;
    letter-spacing: 1px;
    margin-top: 4px;
  }
</style>
</head>
<body>
  <section class="card card--front">
    <div class="brand">
      <span class="brand__square"></span>
      <span class="brand__name">Harborview Estates LLC</span>
    </div>
    <p class="front__web">www.<span class="accent">harborviewest</span>.com</p>
  </section>

  <section class="card card--back">
    <div class="manager">
      <h1 class="manager__name">Marisol Vega</h1>
      <p class="manager__title">Resident Manager</p>
    </div>
    <span class="divider"></span>
    <ul class="contacts">
      <li>
        <svg viewBox="0 0 16 16" fill="var(--brand-blue)"><path d="M3 1l3 3-2 2c1 2 4 5 6 6l2-2 3 3-2 2C7 15 1 9 1 3z"/></svg>
        555-204-1180
      </li>
      <li>
        <svg viewBox="0 0 16 16" fill="var(--brand-blue)"><rect x="4" y="1" width="8" height="4"/><rect x="1" y="6" width="14" height="6" rx="1"/><rect x="4" y="10" width="8" height="5"/></svg>
        555-204-1181
      </li>
      <li>
        <svg viewBox="0 0 16 16" fill="none" stroke="var(--brand-blue)" stroke-width="1.6"><rect x="4" y="1" width="8" height="14" rx="1"/><line x1="7" y1="12.5" x2="9" y2="12.5"/></svg>
        555-318-4620
      </li>
      <li>
        <svg viewBox="0 0 16 16" fill="var(--brand-blue)"><path d="M1 4h14v9H1z"/><path d="M1 4l7 5 7-5" stroke="var(--card-black)" stroke-width="1.4" fill="none"/></svg>
        marisol@harborviewest.com
      </li>
      <li>
        <svg viewBox="0 0 16 16" fill="none" stroke="var(--brand-blue)" stroke-width="1.4"><circle cx="8" cy="8" r="6.5"/><ellipse cx="8" cy="8" rx="3" ry="6.5"/><line x1="1.5" y1="8" x2="14.5" y2="8"/></svg>
        <span>www.<span class="accent">harborviewest</span>.com</span>
      </li>
    </ul>
    <div class="property">
      <h2 class="property__name">Bayside Court Apartments</h2>
      <p class="property__address">2480 Linden Avenue Bayview, CA 90210</p>
    </div>
  </section>
</body>
</html>
```